Revamp of existing namecard

Existingly, i've got a namecard that i would like to retain the main design. but there are some changes in my company and i would need to do some amendments to it.

We are a money transfer and money exchange company.
I need 2 different types of name card.
1. For individual name cards
the front to put the following:
Company name and logo
English Name, Chinese Name appointment
Mobile Number, Email and Website.
2 License number under the logo and name

the back of the name card to put
8 address: 7 Singapore and 1 Hong Kong branch addresses
8 Mobile Number of the corresponding addresses.

We would like to retain the name card front design
the name card back design can change but color to retain.

2nd name card is generic name card
Front:
Company name and logo
Branch Mobile Number, Branch Address, Email and Website.

Industry/Entity Type

remittance and money exchange

Contact Information for Business Card

I need 2 different types of name card. 1. For individual name cards the front to put the following: Company name and logo English Name, Chinese Name appointment Mobile Number, Email and Website. 2 License number under the logo and name the back of the name card to put 8 address: 7 Singapore and 1 Hong Kong branch addresses 8 Mobile Number of the corresponding addresses. We would like to retain the name card front design the name card back design can change but color to retain. 2nd name card is generic name card Front: the front to put the following: Company name and logo Branch Mobile Number, Branch Address, Email and Website. 2 License number under the logo and name

Requirements
Must have
• I need 2 different types of name card. 1. For individual name cards the front to put the following: Company name and logo English Name, Chinese Name appointment Mobile Number, Email and Website. 2 License number under the logo and name the back of the name card to put 8 address: 7 Singapore and 1 Hong Kong branch addresses 8 Mobile Number of the corresponding addresses. We would like to retain the name card front design the name card back design can change but color to retain. 2nd name card is generic name card Front: the front to put the following: Company name and logo Branch Mobile Number, Branch Address, Email and Website. 2 License number under the logo and name
Nice to have
• use back color code

```html
<!DOCTYPE html>
<html lang="en">
<head>
<meta charset="UTF-8">
<title>Vantora Name Cards</title>
<link href="https://fonts.googleapis.com/css2?family=Montserrat:wght@400;500;600;700&family=Noto+Sans+TC:wght@700&display=swap" rel="stylesheet">
<style>
  :root {
    --ink: #2d3540;
    --aqua: #7fcbdb;
    --paper: #ffffff;
    --frame: #9a9a9a;
    --map-tone: #ececec;
    --map-edge: #f7f7f7;
  }
  * { box-sizing: border-box; margin: 0; padding: 0; }
  html, body { width: 1055px; height: 1200px; overflow: hidden; background: var(--paper); }
  body { position: relative; font-family: "Montserrat", sans-serif; color: var(--ink); }

  .card-title {
    position: absolute; top: 198px; width: 429px; text-align: center;
    font-size: 24px; font-weight: 400; color: #111;
  }
  .card {
    position: absolute; top: 240px; width: 429px; height: 253px;
    border: 1px solid var(--frame); background: var(--paper); overflow: hidden;
  }
  .card--individual, .title--individual { left: 76px; }
  .card--branch, .title--branch { left: 548px; }

  .world-map {
    position: absolute; left: 15px; top: 19px; width: 397px; height: 207px;
    background: radial-gradient(ellipse at center, var(--map-tone) 0%, var(--map-edge) 75%, transparent 100%);
  }

  .brand { position: absolute; display: flex; align-items: center; gap: 8px; }
  .brand-dot { border-radius: 50%; background: var(--aqua); }
  .brand-name { font-weight: 700; color: var(--ink); letter-spacing: 0.5px; }

  .card--individual .brand { left: 192px; top: 26px; }
  .card--individual .brand-dot { width: 30px; height: 30px; }
  .card--individual .brand-name { font-size: 29px; }

  .person { position: absolute; left: 25px; top: 105px; }
  .person-name { font-size: 18px; font-weight: 700; line-height: 22px; }
  .person-name-zh { font-family: "Noto Sans TC", sans-serif; font-size: 17px; font-weight: 700; line-height: 21px; }
  .person-role { font-size: 11px; font-weight: 500; color: var(--aqua); line-height: 16px; }

  .contact-list { position: absolute; list-style: none; }
  .contact-list li { display: flex; align-items: center; gap: 5px; white-space: nowrap; }
  .contact-icon { width: 10px; height: 10px; flex: none; }

  .card--individual .contact-list { left: 241px; top: 101px; }
  .card--individual .contact-list li { font-size: 11px; font-weight: 500; height: 17px; letter-spacing: 0.6px; }

  .card--branch .brand { left: 131px; top: 47px; }
  .card--branch .brand-dot { width: 25px; height: 25px; }
  .card--branch .brand-name { font-size: 24px; }

  .branch-pin { position: absolute; left: 70px; top: 117px; width: 22px; height: 28px; }
  .branch-name { position: absolute; left: 103px; top: 119px; font-size: 19px; font-weight: 700; white-space: nowrap; }
  .branch-address {
    position: absolute; left: 222px; top: 114px; font-size: 9px; font-weight: 700;
    line-height: 13.5px; font-style: normal; white-space: nowrap;
  }
  .card--branch .contact-list li { font-size: 11.5px; font-weight: 700; height: 18px; letter-spacing: 0.6px; }
  .contact-list--phones { left: 71px; top: 173px; }
  .contact-list--web { left: 210px; top: 173px; }

  .seal-row { position: absolute; left: 0; top: 650px; width: 1055px; height: 230px; }
  .seal-arc-text { font-family: "Montserrat", sans-serif; font-weight: 500; }
  .seal-name { font-size: 21px; letter-spacing: 5px; }
  .seal-license { font-size: 16px; letter-spacing: 1.5px; }
</style>
</head>
<body>

<h2 class="card-title title--individual">Card 1- front</h2>
<h2 class="card-title title--branch">Card 2- front</h2>

<section class="card card--individual">
  <div class="world-map" role="img" aria-label="Dotted world map in light grey behind the card details"></div>
  <div class="brand"><span class="brand-dot"></span><span class="brand-name">VANTORA</span></div>
  <div class="person">
    <p class="person-name">Marcus Lee</p>
    <p class="person-name-zh">李文浩</p>
    <p class="person-role">Director of Business Development</p>
  </div>
  <ul class="contact-list">
    <li><svg class="contact-icon" viewBox="0 0 10 10"><rect x="2.5" y="0.5" width="5" height="9" rx="1" fill="none" stroke="#7fcbdb" stroke-width="1"/></svg>+852 5123 4408</li>
    <li><svg class="contact-icon" viewBox="0 0 10 10"><path d="M2 0.8 L4 2.8 L3 4 Q4.5 6 6 7 L7.2 6 L9.2 8 L7.8 9.4 Q3.5 8.5 0.6 2.2 Z" fill="#7fcbdb"/></svg>+852 574</li>
    <li><svg class="contact-icon" viewBox="0 0 10 10"><rect x="0.5" y="2" width="9" height="6.5" fill="#7fcbdb"/><path d="M0.8 2.3 L5 5.6 L9.2 2.3" fill="none" stroke="#fff" stroke-width="0.9"/></svg>marcus@vantora.com.hk</li>
    <li><svg class="contact-icon" viewBox="0 0 10 10"><circle cx="5" cy="5" r="4.5" fill="#7fcbdb"/><path d="M0.5 5 H9.5 M5 0.5 Q2 5 5 9.5 M5 0.5 Q8 5 5 9.5" fill="none" stroke="#fff" stroke-width="0.6"/></svg>www.vantora.com.hk</li>
  </ul>
</section>

<section class="card card--branch">
  <div class="world-map" role="img" aria-label="Dotted world map in light grey behind the card details"></div>
  <div class="brand"><span class="brand-dot"></span><span class="brand-name">VANTORA</span></div>
  <svg class="branch-pin" viewBox="0 0 22 28"><path d="M11 0 C4.9 0 0 4.9 0 11 C0 18 11 28 11 28 C11 28 22 18 22 11 C22 4.9 17.1 0 11 0 Z" fill="#7fcbdb"/><circle cx="11" cy="10.5" r="4" fill="#fff"/></svg>
  <p class="branch-name">Kai Tak</p>
  <address class="branch-address">Unit 1605, 16th Floor<br>Kestrel Tower<br>48 Marlow Road, Quarry Bay</address>
  <ul class="contact-list contact-list--phones">
    <li><svg class="contact-icon" viewBox="0 0 10 10"><rect x="2.5" y="0.5" width="5" height="9" rx="1" fill="none" stroke="#7fcbdb" stroke-width="1"/></svg>+852 5123 4408</li>
    <li><svg class="contact-icon" viewBox="0 0 10 10"><path d="M2 0.8 L4 2.8 L3 4 Q4.5 6 6 7 L7.2 6 L9.2 8 L7.8 9.4 Q3.5 8.5 0.6 2.2 Z" fill="#7fcbdb"/></svg>+852 5123 4408</li>
  </ul>
  <ul class="contact-list contact-list--web">
    <li><svg class="contact-icon" viewBox="0 0 10 10"><rect x="0.5" y="2" width="9" height="6.5" fill="#7fcbdb"/><path d="M0.8 2.3 L5 5.6 L9.2 2.3" fill="none" stroke="#fff" stroke-width="0.9"/></svg>marcus@vantora.com.hk</li>
    <li><svg class="contact-icon" viewBox="0 0 10 10"><circle cx="5" cy="5" r="4.5" fill="#7fcbdb"/><path d="M0.5 5 H9.5 M5 0.5 Q2 5 5 9.5 M5 0.5 Q8 5 5 9.5" fill="none" stroke="#fff" stroke-width="0.6"/></svg>www.vantora.com.hk</li>
  </ul>
</section>

<svg class="seal-row" viewBox="0 0 1055 230" aria-label="License seals in three colourways">
  <defs>
    <path id="arc-top-1" d="M190 114 A84 84 0 0 1 358 114"/>
    <path id="arc-bottom-1" d="M177 114 A97 97 0 0 0 371 114"/>
    <path id="arc-top-2" d="M443 114 A84 84 0 0 1 611 114"/>
    <path id="arc-bottom-2" d="M430 114 A97 97 0 0 0 624 114"/>
    <path id="arc-top-3" d="M697 114 A84 84 0 0 1 865 114"/>
    <path id="arc-bottom-3" d="M684 114 A97 97 0 0 0 878 114"/>
  </defs>

  <g class="seal seal--light">
    <circle cx="274" cy="114" r="107" fill="#fff" stroke="#2d3540" stroke-width="2.5"/>
    <circle cx="274" cy="114" r="65" fill="#fff" stroke="#2d3540" stroke-width="2.5"/>
    <circle cx="274" cy="114" r="36" fill="#7fcbdb"/>
    <rect x="184" y="109" width="9" height="9" transform="rotate(45 188.5 113.5)" fill="#2d3540"/>
    <rect x="355" y="109" width="9" height="9" transform="rotate(45 359.5 113.5)" fill="#2d3540"/>
    <text class="seal-arc-text seal-name" fill="#2d3540"><textPath href="#arc-top-1" startOffset="50%" text-anchor="middle">VANTORA</textPath></text>
    <text class="seal-arc-text seal-license" fill="#2d3540"><textPath href="#arc-bottom-1" startOffset="50%" text-anchor="middle">04318726 | 04318726</textPath></text>
  </g>

  <g class="seal seal--dark-ring">
    <circle cx="527" cy="114" r="107" fill="#2d3540"/>
    <circle cx="527" cy="114" r="65" fill="#fff"/>
    <circle cx="527" cy="114" r="36" fill="#7fcbdb"/>
    <rect x="437" y="109" width="9" height="9" transform="rotate(45 441.5 113.5)" fill="#fff"/>
    <rect x="608" y="109" width="9" height="9" transform="rotate(45 612.5 113.5)" fill="#fff"/>
    <text class="seal-arc-text seal-name" fill="#fff"><textPath href="#arc-top-2" startOffset="50%" text-anchor="middle">VANTORA</textPath></text>
    <text class="seal-arc-text seal-license" fill="#fff"><textPath href="#arc-bottom-2" startOffset="50%" text-anchor="middle">04318726 | 04318726</textPath></text>
  </g>

  <g class="seal seal--dark-core">
    <circle cx="781" cy="114" r="107" fill="#fff" stroke="#2d3540" stroke-width="2.5"/>
    <circle cx="781" cy="114" r="65" fill="#2d3540"/>
    <circle cx="781" cy="114" r="36" fill="#7fcbdb"/>
    <rect x="691" y="109" width="9" height="9" transform="rotate(45 695.5 113.5)" fill="#2d3540"/>
    <rect x="862" y="109" width="9" height="9" transform="rotate(45 866.5 113.5)" fill="#2d3540"/>
    <text class="seal-arc-text seal-name" fill="#2d3540"><textPath href="#arc-top-3" startOffset="50%" text-anchor="middle">VANTORA</textPath></text>
    <text class="seal-arc-text seal-license" fill="#2d3540"><textPath href="#arc-bottom-3" startOffset="50%" text-anchor="middle">04318726 | 04318726</textPath></text>
  </g>
</svg>

</body>
</html>
```